Pipe Repair Clamps

A double side A4 showing our pipe repair clamps for stopping leaking pipes within seconds. For water , sewage companies, hotels, malls, airports, hosptals, facilities management companies and district cooling companies. Reverse side will show a size chart. Examples of product uploaded

```html
<!DOCTYPE html>
<html lang="en">
<head>
<meta charset="utf-8">
<title>Harborline Pipe Fittings – Pipe Repair Clamps</title>
<link href="https://fonts.googleapis.com/css2?family=Anton&family=Open+Sans:wght@500;600&family=Roboto:ital,wght@0,400;0,500;0,700;0,900;1,900&display=swap" rel="stylesheet">
<style>
  :root {
    --orange: #f7a444;
    --copper: #c97a2e;
    --ink: #0d0d0d;
    --band-blue: #21508f;
    --cyan: #1aa7c9;
    --white: #ffffff;
  }
  * { margin: 0; padding: 0; box-sizing: border-box; }
  html, body { width: 927px; height: 1200px; overflow: hidden; background: var(--white); }
  .flyer { position: relative; width: 927px; height: 1200px; overflow: hidden; background: var(--white); font-family: 'Roboto', sans-serif; }

  .hero-photo {
    position: absolute; left: 0; top: 240px; width: 927px; height: 362px;
    background:
      linear-gradient(160deg, rgba(255,255,255,0) 0%, rgba(255,255,255,0) 40%),
      linear-gradient(165deg, #ffffff 0%, #ffffff 8%, #a87a57 22%, #6b4a33 45%, #3c4f68 62%, #3f7fc0 78%, #dbe9f5 100%);
  }

  .company-name {
    position: absolute; right: 43px; top: 42px;
    font-weight: 700; font-size: 40px; color: var(--orange); letter-spacing: 0.2px; white-space: nowrap;
  }
  .headline {
    position: absolute; right: 46px; top: 98px;
    font-family: 'Anton', sans-serif; font-size: 55px; line-height: 1; color: var(--ink); white-space: nowrap;
  }
  .subhead {
    position: absolute; right: 46px; top: 154px; white-space: nowrap;
    font-weight: 900; font-style: italic; font-size: 46px; color: var(--copper);
  }
  .subhead .for { font-style: normal; font-weight: 500; font-size: 24px; color: var(--ink); margin-right: 8px; }
  .tagline {
    position: absolute; right: 46px; top: 210px; white-space: nowrap;
    font-weight: 500; font-size: 34px; color: var(--ink);
  }
  .tagline .small { font-size: 24px; }
  .tagline .dot { color: var(--band-blue); }

  .brand-mark {
    position: absolute; left: 68px; top: 196px;
    display: flex; align-items: center; gap: 10px;
  }
  .brand-mark .disc { width: 44px; height: 44px; border-radius: 50%; background: var(--ink); }
  .brand-mark .name { font-weight: 900; font-size: 58px; color: var(--ink); line-height: 1; }

  .audience-band {
    position: absolute; left: 0; top: 602px; width: 927px; height: 310px;
    background: var(--band-blue);
  }
  .audience-photo {
    position: absolute; right: 0; top: 0; width: 430px; height: 310px;
    background: linear-gradient(90deg, rgba(33,80,143,1) 0%, #2e6fb8 35%, #4fa6e4 60%, #2a5f9c 85%, #1d4677 100%);
  }
  .band-label {
    position: absolute; left: 26px; top: 262px;
    transform: rotate(-90deg); transform-origin: left top;
    font-weight: 500; font-size: 120px; line-height: 1; color: rgba(255,255,255,0.09); letter-spacing: 4px;
  }
  .audience-list { position: absolute; left: 140px; top: 38px; list-style: none; }
  .audience-list li {
    display: flex; align-items: center; gap: 16px; height: 29.2px;
    font-family: 'Open Sans', sans-serif; font-weight: 500; font-size: 22px; color: var(--white);
  }
  .audience-list svg { width: 28px; height: 24px; flex: none; }

  .cta-rules { position: absolute; top: 958px; height: 28px; }
  .cta-rules.left { left: 0; width: 282px; }
  .cta-rules.right { left: 648px; width: 279px; }
  .cta-rules span { display: block; height: 4px; background: var(--copper); margin-bottom: 8px; }
  .cta-title {
    position: absolute; left: 0; width: 927px; top: 940px; text-align: center;
    font-weight: 500; font-size: 50px; color: var(--ink);
  }
  .phone {
    position: absolute; left: 0; width: 927px; top: 995px; text-align: center;
    font-weight: 700; font-size: 116px; color: var(--copper); line-height: 1.1; letter-spacing: 1px;
  }
  .website {
    position: absolute; left: 0; width: 927px; top: 1110px; text-align: center;
    font-weight: 700; font-size: 36px; color: var(--cyan); letter-spacing: 9px;
  }
</style>
</head>
<body>
<main class="flyer">
  <div class="hero-photo" role="img" aria-label="Photo of a leaking copper pipe fitted with a repair clamp, water splashing, with product shots of three pipe repair clamps"></div>

  <div class="brand-mark">
    <span class="disc"></span>
    <span class="name">HPF</span>
  </div>

  <h2 class="company-name">HARBORLINE PIPE FITTINGS</h2>
  <h1 class="headline">PIPE REPAIR CLAMPS</h1>
  <p class="subhead"><span class="for">FOR</span>STOPPING LEAKING</p>
  <p class="tagline">PIPES <span class="small">WITHIN</span> SECONDS<span class="dot">.</span></p>

  <section class="audience-band">
    <div class="audience-photo" role="img" aria-label="Close-up photo of water spraying from a damaged pipe"></div>
    <span class="band-label">FOR</span>
    <ul class="audience-list">
      <li><svg viewBox="0 0 28 24"><path d="M2 13 L10 20 L26 3" fill="none" stroke="#e8892e" stroke-width="5" stroke-linecap="round" stroke-linejoin="round"/></svg>Water</li>
      <li><svg viewBox="0 0 28 24"><path d="M2 13 L10 20 L26 3" fill="none" stroke="#e8892e" stroke-width="5" stroke-linecap="round" stroke-linejoin="round"/></svg>Sewage companies</li>
      <li><svg viewBox="0 0 28 24"><path d="M2 13 L10 20 L26 3" fill="none" stroke="#e8892e" stroke-width="5" stroke-linecap="round" stroke-linejoin="round"/></svg>Hotels</li>
      <li><svg viewBox="0 0 28 24"><path d="M2 13 L10 20 L26 3" fill="none" stroke="#e8892e" stroke-width="5" stroke-linecap="round" stroke-linejoin="round"/></svg>Malls</li>
      <li><svg viewBox="0 0 28 24"><path d="M2 13 L10 20 L26 3" fill="none" stroke="#e8892e" stroke-width="5" stroke-linecap="round" stroke-linejoin="round"/></svg>Airports</li>
      <li><svg viewBox="0 0 28 24"><path d="M2 13 L10 20 L26 3" fill="none" stroke="#e8892e" stroke-width="5" stroke-linecap="round" stroke-linejoin="round"/></svg>Hosptals</li>
      <li><svg viewBox="0 0 28 24"><path d="M2 13 L10 20 L26 3" fill="none" stroke="#e8892e" stroke-width="5" stroke-linecap="round" stroke-linejoin="round"/></svg>Facilities management companies</li>
      <li><svg viewBox="0 0 28 24"><path d="M2 13 L10 20 L26 3" fill="none" stroke="#e8892e" stroke-width="5" stroke-linecap="round" stroke-linejoin="round"/></svg>District cooling companies.</li>
    </ul>
  </section>

  <div class="cta-rules left"><span></span><span></span><span></span></div>
  <div class="cta-rules right"><span></span><span></span><span></span></div>
  <p class="cta-title">CALL US NOW</p>
  <p class="phone">123 456 7890</p>
  <p class="website">WWW.YOURWEBSITE.COM</p>
</main>
</body>
</html>
```